Flalzflyer-Design (Folder)
Da für uns neben einem guten Design ein angenehmer und konstruktiver Dialog sowie Verlässlichkeit von hoher Bedeutung ist, sind wir sehr froh auf dieser Plattform auf "brightloom" gestoßen zu sein. Wir sagen ganz herzlich DANKE!!
Zielgruppe
Zielgruppe im Bereich der Vermietung sind Alleinreisende oder als Paar verreisende Natur- und Nordsee verbundene Feriengäste (ü30) mit dem Urlaubsziel 'Sylt', welche eine persönlich und mit besonderem Schick eingerichtet Ferienwohnung/Ferienapartment in zentraler Lage in Westerland suchen und die es als positiven bzw. interessanten Aspekt sehen, dass die Ferienwohnungen direkt von uns Insulaner angeboten werden und wir als Sylter Familie ebenfalls Vor-Ort mit dem Urlaubern unter dem selben Dach leben (wenn auch nicht in der derselben Wohnung ;) ), ganz gemäß unserem Slogan 'Nordseeurlaub unter einem Dach mit Insulanern'
Aufgabenstellung
Es soll ein Falzflyer (Folder) mit Wickelfalz (siehe ggf. https://www.druckwerk-nord.de/werbemittel/folder.html) designed werden (4/4-farbig Euroskala). Bestehend aus einem Papier Format DIN A4 mit zwei Falzen, sodass sich bei Berücksichtigung von Vor- u. Rückseite 6 Seiten ergeben. Die wesentlichen Texte/Inhalte/Informationen, finden sich hier: https://www.quartiersuche-online.de/481926/ . Neben dem Ferienapartment 'Kompass' w ird von uns die Ferienwohnung 'Wadlen' (friesisch für Seestern) angeboten, ebenfalls im Morgenlicht Sylt HOUSE (EST. 2017).
Preisangaben können unberücksichtigt beliben, da sie dem Folder später über eine gesondere Einlage beigelegt werden sollen.
Im Rahmen des Dateiupload bei entwurfsmarkt werden nur einige der möglichen Fotos bereitgestellt. Sie sollen als Auswahlmöglichkeit dienen. Welche der Fotos Verwendung finden oder nach weiteren nachgefragt wird, soll in Abhängigkeit mit dem Gesamtdesign stehen und zunächst von Ihnen entschieden werden, um ein möglichst ansprechenden und harmonischen Folder kreieren zu können.

```html
<!DOCTYPE html>
<html lang="de">
<head>
<meta charset="utf-8">
<title>Morgenlicht Sylt HOUSE – Folder</title>
<link href="https://fonts.googleapis.com/css2?family=Lato:wght@400;700&family=Arimo:wght@400;700&family=Caveat:wght@400&display=swap" rel="stylesheet">
<style>
:root{
  --blue:#3f90c2;
  --text:#3b3b3b;
  --heading:#4a4a4a;
  --rule:#f3d9d9;
  --paper:#ffffff;
  --icon-label:#555;
}
*{box-sizing:border-box;margin:0;padding:0}
html,body{width:840px;height:1200px;overflow:hidden;background:var(--paper)}
.folder{position:relative;width:840px;height:1200px;color:var(--text);font-family:'Lato',sans-serif}
.abs{position:absolute}
.photo{position:absolute}
.script{position:absolute;font-family:'Caveat',cursive;color:var(--blue);font-weight:400;white-space:nowrap;overflow:hidden;line-height:1.2}
.fold-rule{position:absolute;left:0;top:597px;width:840px;height:4px;background:var(--rule)}
/* top */
.visit-title{left:290px;top:256px;font-size:15.5px;line-height:19px;color:var(--heading);font-weight:700}
.visit-title span{font-weight:400}
.visit-copy{left:290px;top:303px;width:254px;font-size:8.6px;line-height:13.7px}
.visit-copy p+p{margin-top:7px}
.dashed{left:290px;top:448px;width:252px;border-top:1.2px dashed var(--blue)}
.contact{left:290px;top:457px;width:260px;font-size:8.6px;line-height:12.8px}
.contact .gap{margin-top:10px}
.cover-name{left:569px;top:470px;width:257px;text-align:center;font-size:21px;font-weight:700;color:var(--heading)}
.cover-est{left:569px;top:495px;width:257px;text-align:center;font-size:15px;color:var(--heading)}
.welcome{left:569px;top:533px;width:257px;text-align:center;font-size:13.5px;line-height:19px;color:var(--blue);font-weight:400}
.welcome b{font-weight:700}
/* bottom */
.body{position:absolute;font-family:'Arimo',sans-serif;font-size:8.4px;line-height:12.8px}
.body p+p{margin-top:12.8px}
.body b{font-weight:700}
.amenities{position:absolute;display:flex}
.amenity{width:51px;text-align:center;font-family:'Lato',sans-serif;font-size:6.2px;line-height:8.6px;color:var(--icon-label)}
.amenity svg{display:block;margin:0 auto 6px}
</style>
</head>
<body>
<div class="folder">

  <!-- Panel: Details -->
  <div class="photo" role="img" aria-label="Wanddeko mit Herz und Holzhaken" style="left:14px;top:14px;width:86px;height:123px;background:linear-gradient(#e6e4de,#cfcac2)"></div>
  <div class="photo" role="img" aria-label="Holzregal mit Sylt-Schriftzug und Möwe" style="left:103px;top:14px;width:159px;height:123px;background:linear-gradient(120deg,#b9a48a,#8a5a36 60%,#6a2a25)"></div>
  <div class="photo" role="img" aria-label="Fenster mit Blick auf Nachbarhäuser" style="left:14px;top:139px;width:163px;height:123px;background:linear-gradient(#2a4b4f,#7d8d88 50%,#5b4a3c)"></div>
  <div class="photo" role="img" aria-label="Glasregal mit Tassen und Tellern" style="left:179px;top:139px;width:83px;height:123px;background:linear-gradient(#e9ecec,#a9cfd6)"></div>
  <div class="script" style="left:14px;top:280px;width:248px;text-align:center;font-size:26px">Details zum Wohlfühlen</div>
  <div class="photo" role="img" aria-label="Baumwollzweig in einer Tasse" style="left:14px;top:335px;width:166px;height:123px;background:linear-gradient(135deg,#b8b2aa,#e9e4dc)"></div>
  <div class="photo" role="img" aria-label="Frühlingsgesteck vor grüner Wand" style="left:183px;top:335px;width:79px;height:123px;background:linear-gradient(#cfe08a,#8a8c5c)"></div>
  <div class="photo" role="img" aria-label="Garderobe mit Herzanhänger" style="left:14px;top:460px;width:102px;height:123px;background:linear-gradient(90deg,#e7e2da 60%,#b89a1a)"></div>
  <div class="photo" role="img" aria-label="Holztisch mit Windlicht" style="left:119px;top:460px;width:143px;height:123px;background:linear-gradient(135deg,#2e2e2e,#8a7866 60%,#5a4a3c)"></div>

  <!-- Panel: Besuchen Sie uns -->
  <div class="photo" role="img" aria-label="Hausansicht mit Garten und Pflasterweg" style="left:290px;top:14px;width:124px;height:227px;background:linear-gradient(#5f8ed0,#e8e8e8 35%,#c7a060 60%,#6d7a3e)"></div>
  <div class="photo" role="img" aria-label="Hortensien und zwei Tassen auf dem Tisch" style="left:417px;top:14px;width:125px;height:111px;background:linear-gradient(#6f78c2,#3f6a3c 55%,#e6e6ea)"></div>
  <div class="photo" role="img" aria-label="Schwimmen in der Nordsee" style="left:417px;top:128px;width:125px;height:113px;background:linear-gradient(#bfc5c8,#8d959a 55%,#4c5356)"></div>
  <div class="abs visit-title">BESUCHEN SIE UNS<br><span>AUF SYLT.</span></div>
  <div class="abs visit-copy">
    <p>Das Morgenlicht Sylt House (est. 2017) ist in Nachbarschaft des denkmalgeschützten Westerländer Polizeigebäudes (ehem. Amtsgericht) gelegen. Die vorteilhafte Lage ist damit zentral aber ruhig in 2. Reihe in Alt-Westerland.</p>
    <p>Der Bahnhof ist ca. 4-5 Gehminuten, die Fußgängerzone/Fried­richstr. mit div. Einkaufsmöglichkeiten und Restaurants/Cafés ca. 7 Min. und der Strand/die Kurpromenade ca. 12 Min. entfernt. Auch das Schwimmbad Inselbad Nordwelle, das Vitalhaus Westerland (Well­ness) o. die Spielbank sind nah.</p>
  </div>
  <div class="abs dashed"></div>
  <div class="abs contact">
    <div>Familie Morgenlicht</div>
    <div><b>Morgenlicht Sylt HOUSE (EST. 2017)</b></div>
    <div>Dünenstieg 14b, Westerland</div>
    <div class="gap"><b>Wir sind für Sie da</b> · Mo - So &nbsp; 9.00 - 21.00</div>
    <div>Telefon:+49 (0)4651 - 300 5172 · Mobil: +49 (0)171 - 508 2693</div>
    <div>eMail: sylt@morgenlicht.net</div>
    <div>Belegungskalender: sylt.morgenlicht.net</div>
    <div>Mehr Fotos + Preise finden Sie auf: quartiersuche-online.de</div>
    <div>=&gt; Wohin: Morgenlicht Sylt</div>
  </div>

  <!-- Panel: Cover -->
  <div class="photo" role="img" aria-label="Strand mit Strandkörben und Rettungsturm" style="left:569px;top:14px;width:257px;height:377px;background:linear-gradient(#4d86c8,#e8eef4 35%,#2d5f86 47%,#e4d8c2 62%,#9c8a6e)"></div>
  <div class="script" style="left:569px;top:414px;width:257px;text-align:center;font-size:25px">Nordseeurlaub bei Insulanern</div>
  <div class="abs cover-name">Morgenlicht Sylt HOUSE</div>
  <div class="abs cover-est">(EST. 2017)</div>
  <div class="abs welcome">HERZLICH WILLKOMMEN<br><b>BEI FAMILIE MORGENLICHT!</b></div>

  <div class="fold-rule"></div>

  <!-- Panel: Kompass -->
  <div class="script" style="left:14px;top:619px;width:260px;font-size:27px">Ferienapartment 'Kompass'</div>
  <div class="photo" role="img" aria-label="Schlafzimmer mit Einzelbett" style="left:14px;top:660px;width:128px;height:123px;background:linear-gradient(135deg,#cfc8c0,#8a6a50)"></div>
  <div class="photo" role="img" aria-label="Wohnbereich mit Sofa und Kommode" style="left:145px;top:660px;width:126px;height:123px;background:linear-gradient(135deg,#d9d4cc,#4a4646)"></div>
  <div class="body" style="left:14px;top:791px;width:258px">Das Apartment ist seniorengerecht, ebenerdig, kurze Wege, An­sprechpartner im Haus, Bahnhof Westerland fussläufig 5 Min.</div>
  <div class="photo" role="img" aria-label="Grundriss des Apartments Kompass im Erdgeschoss" style="left:20px;top:827px;width:233px;height:122px;background:linear-gradient(90deg,#efeedd 60%,#d4e6f4)"></div>
  <div class="body" style="left:14px;top:955px;width:258px">
    <p><b>Wer Meer hat, braucht weniger, sagt man.</b><br>Die Zimmer persönlich und mit Geschick gestaltet, zeitgemäße Wohneinrichtung, modernes ebenerdiges Duschbad, hochwertige Pantryküche, Smart-TV, Wlan, ansprechendes und vollständiges Geschirr, Außenbereich sowie der persönlichen Nähe zu uns Insulanern.</p>
    <p>Das App. eignet sich für einen längeren Urlaub besonders für 1 Person. Es steht ein Einzelbett im kl. Schlafzimmer zur Verfü­gung. Für einen Aufenthalt von einigen Tagen haben 2 Pers. ebenfalls eine passend schöne Unterkunft (Schlafmöglichkeit auf komfortablen Schlafsofa mit Lattenrost).</p>
  </div>
  <div class="amenities" style="left:10px;top:1124px">
    <div class="amenity"><svg width="38" height="38" viewBox="0 0 38 38"><circle cx="19" cy="19" r="17" fill="none" stroke="var(--blue)" stroke-width="2"/><path d="M10 16a13 13 0 0 1 18 0M13 19.5a8.5 8.5 0 0 1 12 0M16 23a4 4 0 0 1 6 0" fill="none" stroke="var(--blue)" stroke-width="2.2" stroke-linecap="round"/><circle cx="19" cy="26" r="1.8" fill="var(--blue)"/></svg>kostenloses<br>WLAN</div>
    <div class="amenity"><svg width="38" height="38" viewBox="0 0 38 38"><circle cx="19" cy="19" r="17" fill="none" stroke="var(--blue)" stroke-width="2"/><rect x="9" y="19" width="17" height="4" fill="var(--blue)"/><rect x="27" y="19" width="2" height="4" fill="var(--blue)"/><line x1="10" y1="11" x2="28" y2="27" stroke="var(--blue)" stroke-width="2.2"/></svg>Nichtraucher<br>Wohnung</div>
    <div class="amenity"><svg width="38" height="38" viewBox="0 0 38 38"><circle cx="19" cy="19" r="17" fill="none" stroke="var(--blue)" stroke-width="2"/><path d="M12 27V14a7 5 0 0 1 14 0v13M12 20h14M12 27h14" fill="none" stroke="var(--blue)" stroke-width="2"/><path d="M15 14v6M18 12v8M21 12v8M24 14v6" stroke="var(--blue)" stroke-width="1.2"/></svg>Strandkorb<br>vorhanden</div>
    <div class="amenity"><svg width="38" height="38" viewBox="0 0 38 38"><circle cx="19" cy="19" r="17" fill="none" stroke="var(--blue)" stroke-width="2"/><rect x="11" y="10" width="16" height="18" rx="1.5" fill="none" stroke="var(--blue)" stroke-width="2"/><line x1="11" y1="15" x2="27" y2="15" stroke="var(--blue)" stroke-width="1.5"/><path d="M14 20h10M14 23h10" stroke="var(--blue)" stroke-width="1.5"/></svg>Geschirrspüler<br>vorhanden</div>
    <div class="amenity"><svg width="38" height="38" viewBox="0 0 38 38"><circle cx="19" cy="19" r="17" fill="none" stroke="var(--blue)" stroke-width="2"/><path d="M10 13v14M10 22h18v5" fill="none" stroke="var(--blue)" stroke-width="2"/><circle cx="14" cy="19" r="2" fill="var(--blue)"/><rect x="17" y="17" width="11" height="4" rx="1" fill="var(--blue)"/></svg>Bettwäsche &amp;<br>Handtücher</div>
  </div>

  <!-- Panel: About -->
  <div class="script" style="left:298px;top:621px;width:254px;font-size:27px">Wer sind wir</div>
  <div class="body" style="left:298px;top:662px;width:254px">Wir sind eine 3-köpfige Familie, die ganzjährig im Morgenlicht Sylt HOUSE (Est. 2017) lebt und auf Wunsch gerne helfend mit Urlaubstipps und Klönschnack zur Verfügung steht. Unsere Tochter geht in Westerland zur Schule.</div>
  <div class="script" style="left:298px;top:723px;width:254px;font-size:27px">Warum sind wir Gastgeber</div>
  <div class="body" style="left:298px;top:765px;width:254px">Weil wir als offene Menschen neue Begegnungen schätzen und so unseren Traum - ganzjährig auf Sylt zu leben - in die Tat umsetzen können.</div>
  <div class="photo" role="img" aria-label="In den Sand geschriebener Schriftzug" style="left:298px;top:810px;width:83px;height:123px;background:linear-gradient(#b9b3aa,#8c8680)"></div>
  <div class="photo" role="img" aria-label="Dünen und Strand von oben" style="left:384px;top:810px;width:166px;height:123px;background:linear-gradient(#7fb0e0,#c8dced 45%,#cdbfa4 60%,#7c8a46)"></div>
  <div class="photo" role="img" aria-label="Spaziergänger am Strand unter Wolken" style="left:298px;top:936px;width:150px;height:99px;background:linear-gradient(#6c9ed4,#dfe6ec 55%,#a9a090)"></div>
  <div class="photo" role="img" aria-label="Sonnenuntergang über den Dünen" style="left:451px;top:936px;width:99px;height:99px;background:linear-gradient(#4b6a9a,#e9a25a 55%,#2e2a28)"></div>
  <div class="script" style="left:298px;top:1052px;width:254px;font-size:27px">Unser Service für Sie</div>
  <div class="body" style="left:298px;top:1093px;width:254px">
    <p>Kostenloser Hol-/Bringservice Bahnhof Westerland nach Absprache möglich.</p>
    <p>Das Wäschepaket beinhaltet: Bettwäsche, Laken, Handtuch (2x), Duschtuch, Badvorleger, Geschirrtuch.</p>
    <p>Endreinigung inklusive.</p>
  </div>

  <!-- Panel: Wadlen -->
  <div class="script" style="left:577px;top:619px;width:252px;font-size:27px">Ferienwohnung 'Wadlen'</div>
  <div class="photo" role="img" aria-label="Schlafzimmer mit Doppelbett" style="left:577px;top:660px;width:124px;height:123px;background:linear-gradient(135deg,#7a6a5a,#e9e6e2 55%,#c94a3a)"></div>
  <div class="photo" role="img" aria-label="Badezimmer mit Blumendeko" style="left:704px;top:660px;width:122px;height:123px;background:linear-gradient(135deg,#e8e6e0,#5a4a3e 55%,#3c6a52)"></div>
  <div class="body" style="left:577px;top:791px;width:252px">Das Apartment ist seniorengerecht, ebenerdig, kurze Wege, Ansprechpartner im Haus, Bahnhof Westerland fussläufig.</div>
  <div class="photo" role="img" aria-label="Grundriss der Ferienwohnung Wadlen im ersten Obergeschoss" style="left:632px;top:827px;width:139px;height:122px;background:linear-gradient(#f6cbc3,#f0b6ab)"></div>
  <div class="body" style="left:577px;top:955px;width:252px">
    <p><b>Wer Meer hat, braucht weniger, sagt man.</b><br>Die Zimmer persönlich und mit Geschick gestaltet, zeitgemäße Wohneinrichtung, modernes ebenerdiges Duschbad, hoch­wertige Pantryküche, Smart-TV, Wlan, ansprechendes und vollständiges Geschirr, Außenbereich sowie der persönlichen Nähe zu uns Insulanern.</p>
    <p>Das App. eignet sich für einen längeren Urlaub besonders für 1 Person. Es steht ein Einzelbett im kl. Schlafzimmer zur Ver­fügung. Für einen Aufenthalt von einigen Tagen haben 2 Pers. ebenfalls eine passend schöne Unterkunft (Schlafmöglichkeit auf komfortablen Schlafsofa mit Lattenrost).</p>
  </div>
  <div class="amenities" style="left:573px;top:1118px">
    <div class="amenity"><svg width="38" height="38" viewBox="0 0 38 38"><circle cx="19" cy="19" r="17" fill="none" stroke="var(--blue)" stroke-width="2"/><path d="M10 16a13 13 0 0 1 18 0M13 19.5a8.5 8.5 0 0 1 12 0M16 23a4 4 0 0 1 6 0" fill="none" stroke="var(--blue)" stroke-width="2.2" stroke-linecap="round"/><circle cx="19" cy="26" r="1.8" fill="var(--blue)"/></svg>kostenloses<br>WLAN</div>
    <div class="amenity"><svg width="38" height="38" viewBox="0 0 38 38"><circle cx="19" cy="19" r="17" fill="none" stroke="var(--blue)" stroke-width="2"/><rect x="9" y="19" width="17" height="4" fill="var(--blue)"/><rect x="27" y="19" width="2" height="4" fill="var(--blue)"/><line x1="10" y1="11" x2="28" y2="27" stroke="var(--blue)" stroke-width="2.2"/></svg>Nichtraucher<br>Wohnung</div>
    <div class="amenity"><svg width="38" height="38" viewBox="0 0 38 38"><circle cx="19" cy="19" r="17" fill="none" stroke="var(--blue)" stroke-width="2"/><rect x="10" y="11" width="18" height="12" rx="1.5" fill="none" stroke="var(--blue)" stroke-width="2"/><path d="M19 23v4M14 27h10" stroke="var(--blue)" stroke-width="2"/></svg>Smart TV<br>vorhanden</div>
    <div class="amenity"><svg width="38" height="38" viewBox="0 0 38 38"><circle cx="19" cy="19" r="17" fill="none" stroke="var(--blue)" stroke-width="2"/><rect x="11" y="10" width="16" height="18" rx="1.5" fill="none" stroke="var(--blue)" stroke-width="2"/><line x1="11" y1="15" x2="27" y2="15" stroke="var(--blue)" stroke-width="1.5"/><path d="M14 20h10M14 23h10" stroke="var(--blue)" stroke-width="1.5"/></svg>Geschirrspüler<br>vorhanden</div>
    <div class="amenity"><svg width="38" height="38" viewBox="0 0 38 38"><circle cx="19" cy="19" r="17" fill="none" stroke="var(--blue)" stroke-width="2"/><path d="M10 13v14M10 22h18v5" fill="none" stroke="var(--blue)" stroke-width="2"/><circle cx="14" cy="19" r="2" fill="var(--blue)"/><rect x="17" y="17" width="11" height="4" rx="1" fill="var(--blue)"/></svg>Bettwäsche &amp;<br>Handtücher</div>
  </div>

</div>
</body>
</html>
```